Business Card Design Project

2 sided business card utilizing existing logo
- English on one side, Arabic on the other side (both English and Arabic text will be provided)
Same color scheme as logo
Information included will be: name, title, email, phone, address and website (www.veltrimond.com)
Updates

Target Market(s)

We are a Systems Integration Company

Industry/Entity Type

Business

Font styles to use
Serif
Sans Serif

Requirements
Should not have
• We prefer using the flat logo rather than one with shadow/3D effect

```html
<!DOCTYPE html>
<html lang="en">
<head>
<meta charset="UTF-8">
<title>Veltrimond Business Card</title>
<link href="https://fonts.googleapis.com/css2?family=Questrial&display=swap" rel="stylesheet">
<style>
  :root {
    --backdrop: #b8b8b8;
    --card: #ffffff;
    --brand-red: #e31e24;
    --brand-red-dark: #b3151b;
    --ink: #1a1a1a;
  }
  * { margin: 0; padding: 0; box-sizing: border-box; }
  html, body {
    width: 1200px; height: 900px; overflow: hidden;
    background: var(--backdrop);
    font-family: "Questrial", "Century Gothic", sans-serif;
  }
  .card {
    position: absolute; left: 150px; top: 175px;
    width: 900px; height: 550px;
    background: var(--card);
    border-radius: 42px;
  }
  .brand {
    position: absolute; top: 190px; left: 0; right: 0;
    display: flex; align-items: center; justify-content: center; gap: 16px;
  }
  .brand-dot {
    width: 20px; height: 20px; border-radius: 50%;
    background: var(--brand-red);
  }
  .brand-name {
    color: var(--brand-red);
    font-size: 44px; letter-spacing: 0;
  }
  .band {
    position: absolute; left: 0; right: 0; top: 298px; height: 20px;
    background: linear-gradient(to bottom, var(--brand-red) 0 45%, var(--brand-red-dark) 45% 100%);
  }
  .person {
    position: absolute; right: 490px; top: 370px; text-align: right;
  }
  .person-name { color: var(--brand-red); font-size: 34px; }
  .person-title { color: var(--ink); font-size: 25px; margin-top: 4px; }
  .divider {
    position: absolute; left: 440px; top: 345px; width: 2px; height: 165px;
    background: var(--ink);
  }
  .contacts {
    position: absolute; left: 465px; top: 345px; list-style: none;
    color: var(--ink); font-size: 24px; line-height: 1.3;
  }
  .contacts li { display: flex; align-items: flex-start; gap: 10px; margin-bottom: 2px; }
  .contacts svg { width: 26px; height: 26px; flex: none; margin-top: 3px; fill: var(--brand-red); }
</style>
</head>
<body>
  <div class="card">
    <div class="brand">
      <div class="brand-dot"></div>
      <div class="brand-name">Veltrimond</div>
    </div>
    <div class="band"></div>
    <div class="person">
      <div class="person-name">Darel Voss</div>
      <div class="person-title">manager</div>
    </div>
    <div class="divider"></div>
    <ul class="contacts">
      <li>
        <svg viewBox="0 0 24 24"><path d="M6.6 10.8c1.4 2.8 3.8 5.1 6.6 6.6l2.2-2.2c.3-.3.7-.4 1-.2 1.1.4 2.3.6 3.6.6.6 0 1 .4 1 1V20c0 .6-.4 1-1 1C10.6 21 3 13.4 3 4c0-.6.4-1 1-1h3.5c.6 0 1 .4 1 1 0 1.3.2 2.5.6 3.6.1.3 0 .7-.2 1z"/></svg>
        <span>(916) 555-0142</span>
      </li>
      <li>
        <svg viewBox="0 0 24 24"><path d="M2 8l10 6 10-6v12H2z"/><path d="M2 6h20l-10 6z"/></svg>
        <span>info@veltrimond.com</span>
      </li>
      <li>
        <svg viewBox="0 0 24 24"><path d="M12 2a10 10 0 1 0 0 20 10 10 0 0 0 0-20zm0 2c.9 1.2 1.6 2.5 2 4h-4c.4-1.5 1.1-2.8 2-4zM4.3 14a8 8 0 0 1 0-4h3.3c-.1.7-.1 1.3-.1 2s0 1.3.1 2zm.8 2h3c.3 1.3.8 2.4 1.4 3.5A8 8 0 0 1 5.1 16zm3-8h-3a8 8 0 0 1 4.4-3.5C8.9 5.6 8.4 6.7 8.1 8zM12 20c-.9-1.2-1.6-2.5-2-4h4c-.4 1.5-1.1 2.8-2 4zm2.3-6H9.7c-.1-.7-.2-1.3-.2-2s.1-1.3.2-2h4.6c.1.7.2 1.3.2 2s-.1 1.3-.2 2zm.2 5.5c.6-1.1 1.1-2.2 1.4-3.5h3a8 8 0 0 1-4.4 3.5zm1.9-5.5c.1-.7.1-1.3.1-2s0-1.3-.1-2h3.3a8 8 0 0 1 0 4zm-.5-6c-.3-1.3-.8-2.4-1.4-3.5A8 8 0 0 1 18.9 8z"/></svg>
        <span>www.veltrimond.com</span>
      </li>
      <li>
        <svg viewBox="0 0 24 24"><path d="M12 3l10 9h-3v9h-5v-6h-4v6H5v-9H2z"/></svg>
        <span>4120 Marlow Avenue, Suite D,<br>Fairbrook, CA 95870</span>
      </li>
    </ul>
  </div>
</body>
</html>
```